Veltrane Group Business Card Design

The CEO is looking for a new trendy look for his business card.
You can stay with current branding or come up with something new/creative. It can be 3D, including Medical Office buildings. You can use our logo in a variety of colors. Please include name, title, company name, company website, email address, cell number

Target Market(s)

Real Estate Development and Construction

Industry/Entity Type

Health care real estate

Contact Information for Business Card

Rohesh Kamdar, CEO M-604.781.2249 E-roheshkamdar@veltrane.com Address:4180 Lindqvist Ave, Tampa, FL 33482 www.veltrane.com

Font styles to use
Other font styles liked:
• Be creative

Requirements
Must have
• Creative, trendy look
Nice to have
• Please go to our website to get a feel- www. veltrane.com
Should not have
• small fonts

```html
<!DOCTYPE html>
<html lang="en">
<head>
<meta charset="utf-8">
<title>Veltrane Group — Business Card</title>
<link rel="stylesheet" href="https://fonts.googleapis.com/css2?family=Montserrat:wght@400;500;700&display=swap">
<style>
  :root {
    --backdrop: #1f1f1f;
    --card: #ffffff;
    --ink: #111111;
    --ink-soft: #2a2a2a;
    --radius: 26px;
  }
  * { box-sizing: border-box; margin: 0; padding: 0; }
  html, body {
    width: 1200px;
    height: 874px;
    overflow: hidden;
    background: var(--backdrop);
    font-family: "Montserrat", sans-serif;
    color: var(--ink);
  }
  .stage {
    width: 1200px;
    height: 874px;
    display: flex;
    flex-direction: column;
    align-items: center;
    justify-content: center;
    gap: 40px;
  }
  .card {
    width: 640px;
    height: 366px;
    background: var(--card);
    border-radius: var(--radius);
    position: relative;
  }
  .card-front {
    display: flex;
    align-items: center;
    justify-content: center;
  }
  .company-name {
    font-weight: 700;
    font-size: 56px;
    line-height: 1;
    letter-spacing: -1px;
    color: var(--ink);
    white-space: nowrap;
  }
  .card-back .contact-block {
    position: absolute;
    left: 110px;
    top: 150px;
    display: flex;
    align-items: stretch;
    gap: 16px;
  }
  .identity {
    text-align: right;
    padding-top: 2px;
  }
  .identity .person-name {
    font-weight: 700;
    font-size: 21px;
    color: var(--ink);
  }
  .identity .person-title {
    font-weight: 400;
    font-size: 15px;
    margin-top: 4px;
    color: var(--ink-soft);
  }
  .divider {
    width: 2px;
    background: var(--ink);
  }
  .channels {
    list-style: none;
    display: flex;
    flex-direction: column;
    gap: 7px;
    font-size: 15px;
    font-weight: 500;
    color: var(--ink-soft);
  }
  .channels li {
    display: flex;
    align-items: center;
    gap: 10px;
  }
  .channels svg {
    width: 14px;
    height: 14px;
    fill: var(--ink);
    flex: none;
  }
  .address {
    position: absolute;
    left: 110px;
    top: 282px;
    font-size: 15px;
    font-weight: 500;
    color: var(--ink-soft);
  }
</style>
</head>
<body>
  <main class="stage">
    <section class="card card-front" aria-label="Card front">
      <h1 class="company-name">Veltrane Group</h1>
    </section>

    <section class="card card-back" aria-label="Card back">
      <div class="contact-block">
        <div class="identity">
          <p class="person-name">Rohesh Kamdar</p>
          <p class="person-title">CEO</p>
        </div>
        <div class="divider"></div>
        <ul class="channels">
          <li>
            <svg viewBox="0 0 24 24" aria-hidden="true"><path d="M6.6 10.8a15.1 15.1 0 0 0 6.6 6.6l2.2-2.2a1 1 0 0 1 1-.25 11.4 11.4 0 0 0 3.6.57 1 1 0 0 1 1 1V20a1 1 0 0 1-1 1A17 17 0 0 1 3 4a1 1 0 0 1 1-1h3.5a1 1 0 0 1 1 1c0 1.25.2 2.45.57 3.6a1 1 0 0 1-.25 1z"/></svg>
            <span>604.781.2249</span>
          </li>
          <li>
            <svg viewBox="0 0 24 24" aria-hidden="true"><path d="M2 5h20v14H2z"/><path d="M3 6.2l9 6.3 9-6.3V5H3z" fill="#fff"/></svg>
            <span>roheshkamdar@veltrane.com</span>
          </li>
          <li>
            <svg viewBox="0 0 24 24" aria-hidden="true"><circle cx="12" cy="12" r="10"/><path d="M2 12h20M12 2c3 3 3 17 0 20M12 2c-3 3-3 17 0 20" fill="none" stroke="#fff" stroke-width="1.6"/></svg>
            <span>www.veltrane.com</span>
          </li>
        </ul>
      </div>
      <p class="address">4180 Lindqvist Ave, Tampa, FL 33482</p>
    </section>
  </main>
</body>
</html>
```